Business card for Crestline Bathrooms

Please design a business card for our bathroom renovation business. You can use my existing logo, but if you have an idea to modernize it, I would like to see it. Please see attached files first. I would like to use the blue and the orange theme. I like the concept of using the shower head in the logo. Please find following a design (or two) that I have been trying to create with my limited resources. That design was for a sign, but I was going to adopt it and use it as a business card as well. I like the concept of the water splash but I don’t think it “flows” nicely together with the logo. Another thought is that maybe creating the logo out of water splash could work and have a dramatic effect (like the water text and the butterfly picture attached with similar background instead of white). If the above doesn’t work I would like to see a modern simplified design. One of the attached files named as the unwanted business card has all the details that I want included in the business card. Please note that it is two sided.
Updates

I am very thankful for the designs that I have received, but they are very similar and only a couple of attempts to do something with the water splash as per my original brief. Modernizing the logo and having it made out of out of water splash with the orange as color accent could work and have a dramatic effect (like the water text and the butterfly picture attached with similar background instead of white). Please do not use the butterfly itself! This is just an example that images can be created out of water splash.

Contact Information for Business Card

all the details are on the unwonted business card file included

Colors
3176b5

Requirements
Nice to have
• Copied from the brief:
• ... maybe creating the logo out of water splash could work and have a dramatic effect (like the water text and the butterfly picture attached with similar background instead of white). Please do not use the butterfly itself!
Should not have
• I am getting designs with a butterfly. The butterfly picture was an example of creating something from a water splash. The butterfly itself has no association with anything other than the concept of creating a logo out of water splash. Sorry, I thought I was clear in the brief.

```html
<!DOCTYPE html>
<html lang="en">
<head>
<meta charset="utf-8">
<title>Crestline Bathrooms — Business Card</title>
<link rel="stylesheet" href="https://fonts.googleapis.com/css2?family=Roboto:wght@400;700&family=Patrick+Hand&display=swap">
<style>
  :root {
    --stage: #e4e4e4;
    --navy: #182f55;
    --navy-deep: #12244a;
    --water-light: #cfe0f2;
    --water-mid: #4d79ad;
    --accent: #ec7b6b;
    --white: #ffffff;
  }
  * { box-sizing: border-box; margin: 0; padding: 0; }
  html, body { width: 1200px; height: 960px; overflow: hidden; }
  body {
    background: var(--stage);
    position: relative;
    font-family: "Roboto", Arial, sans-serif;
    color: var(--white);
  }
  .card {
    position: absolute;
    width: 600px;
    height: 342px;
    background: var(--navy);
    overflow: hidden;
    box-shadow: 2px 3px 4px rgba(0,0,0,0.35);
  }
  .card--front { left: 302px; top: 125px; }
  .card--back  { left: 300px; top: 494px; }

  .splash { position: absolute; }
  .card--front .splash {
    left: 0; top: 0; width: 300px; height: 342px;
    background:
      radial-gradient(ellipse 140px 70px at 90px 320px, rgba(225,236,248,0.85), rgba(120,160,205,0.35) 60%, transparent 100%),
      radial-gradient(ellipse 90px 160px at 40px 250px, rgba(170,200,230,0.45), transparent 80%),
      linear-gradient(90deg, rgba(60,100,150,0.45), transparent 85%),
      radial-gradient(ellipse 120px 80px at 100px 30px, rgba(130,170,215,0.35), transparent 80%);
  }
  .card--back .splash {
    right: 0; top: 0; width: 300px; height: 342px;
    background:
      radial-gradient(ellipse 150px 75px at 200px 320px, rgba(225,236,248,0.85), rgba(120,160,205,0.35) 60%, transparent 100%),
      radial-gradient(ellipse 80px 160px at 265px 240px, rgba(170,200,230,0.5), transparent 80%),
      linear-gradient(270deg, rgba(60,100,150,0.45), transparent 85%),
      radial-gradient(ellipse 130px 80px at 170px 30px, rgba(130,170,215,0.35), transparent 80%);
  }

  .services {
    position: absolute;
    right: 46px; top: 60px;
    list-style: none;
    text-align: right;
    font-size: 15px;
    line-height: 24px;
  }
  .services li::after {
    content: "";
    display: inline-block;
    width: 6px; height: 6px;
    margin-left: 8px;
    border-radius: 50%;
    background: var(--accent);
    vertical-align: middle;
  }

  .memberships {
    position: absolute;
    right: 44px; top: 262px;
    display: flex; align-items: center; gap: 28px;
  }
  .badge { background: var(--white); }
  .badge--round { width: 32px; height: 34px; border-radius: 8px; }
  .badge--wide { width: 118px; height: 26px; border-radius: 2px; }

  .brand {
    position: absolute;
    left: 112px; top: 66px;
    display: flex; align-items: center; gap: 10px;
    font-size: 24px; font-weight: 700;
    color: var(--white);
  }
  .brand__dot { width: 14px; height: 14px; border-radius: 50%; background: var(--accent); }

  .contact { position: absolute; left: 26px; top: 176px; }
  .contact__name {
    font-family: "Patrick Hand", cursive;
    font-size: 25px;
    color: var(--accent);
    font-weight: 400;
    margin-bottom: 8px;
  }
  .contact__line {
    display: flex; align-items: center; gap: 6px;
    font-size: 17px; line-height: 21px;
  }
  .contact__line--phones { font-weight: 700; font-size: 18px; }
  .contact__line svg { width: 14px; height: 14px; fill: var(--accent); flex: none; }
  .contact__abn { font-size: 13.5px; margin-top: 5px; }
</style>
</head>
<body>

<section class="card card--front" aria-label="Card front">
  <div class="splash" role="img" aria-label="Photograph of a water splash with falling droplets"></div>
  <ul class="services">
    <li>Complete Bathroom Renovations &amp; Remodelling</li>
    <li>Professional Service From Concept To Completion</li>
    <li>Highly Skilled &amp; Qualified Tradespeople</li>
    <li>All Work Guaranteed</li>
  </ul>
  <div class="memberships">
    <div class="badge badge--round" role="img" aria-label="Industry association membership badge"></div>
    <div class="badge badge--wide" role="img" aria-label="Builders association membership badge"></div>
  </div>
</section>

<section class="card card--back" aria-label="Card back">
  <div class="splash" role="img" aria-label="Photograph of a water splash with falling droplets"></div>
  <div class="brand"><span class="brand__dot"></span>Crestline Bathrooms</div>
  <div class="contact">
    <h1 class="contact__name">Daniel Porter</h1>
    <p class="contact__line contact__line--phones">
      <svg viewBox="0 0 14 14"><path d="M4 0h6a1 1 0 0 1 1 1v12a1 1 0 0 1-1 1H4a1 1 0 0 1-1-1V1a1 1 0 0 1 1-1zm0 2v9h6V2z"/></svg>
      0400 318 274 |
      <svg viewBox="0 0 14 14"><path d="M1 5c0-2 3-3 6-3s6 1 6 3v1h-3V5H4v1H1zm2 2h8l1 6H2z"/></svg>
      6190 4427
    </p>
    <p class="contact__line">
      <svg viewBox="0 0 14 14"><path d="M7 1a6 6 0 1 0 3 11v-1.6A4.5 4.5 0 1 1 11.5 7v1a1 1 0 0 1-2 0V4H8v.5A3 3 0 1 0 8.7 9.6 2.4 2.4 0 0 0 13 8V7a6 6 0 0 0-6-6zm0 4.5a1.5 1.5 0 1 1 0 3 1.5 1.5 0 0 1 0-3z"/></svg>
      daniel@crestlinebathrooms.com.au
    </p>
    <p class="contact__line">
      <svg viewBox="0 0 14 14"><path d="M7 1a6 6 0 1 0 0 12A6 6 0 0 0 7 1zm-1 2.2c.6.5.4 1.4-.3 1.8-.8.5-.6 1.5.3 1.7 1 .2 1.3 1.3.7 2-.5.6-.3 1.6.4 2.1A4.6 4.6 0 0 1 6 3.2zm3 .6a4.6 4.6 0 0 1 1.8 5.5c-.7-.5-1.6-.4-2-.9-.4-.6.4-1.3 0-1.9-.4-.5-1.3-.4-1.3-1.1 0-.6.9-.9 1.5-1.6z"/></svg>
      crestlinebathrooms.com.au
    </p>
    <p class="contact__line">
      <svg viewBox="0 0 14 14"><path d="M1 3h12v1.2L7 8 1 4.2zm0 2.6 6 3.8 6-3.8V11H1z"/></svg>
      PO Box 418, Kingsford Vale 2600
    </p>
    <p class="contact__abn">ABN 52 604 219 377</p>
  </div>
</section>

</body>
</html>
```